Wellbrook Talking Therapies Hub Swindon

We need a design for magazine advert, ideally high resolution to advertise our counselling centre. we would like this to include a photo of two people talking, as if in a counselling session. See our logo and colour range on our website. www.wbtth-swindon.co.uk
The photo should not include cups of coffee, clipboards, desks, people touching. it needs to be two people in armchairs sympathetically listening and looking at each other.
The font type is Great Vibes on the logo. Our design should communicate a centre of excellence delivering high quality, professional services in stylishly furnished surroundings.

Hello Everyone We have had a number of designs that look quite promising but are missing the brief. Can I reiterate that we need a photograph of 2 people seated talking to each other in a sincere way. There shouldn't be office chairs but comfortable chairs. There should be no physical contact. There should be no clipboards.Thank you very muchHeather Added Sunday, March 12, 2017

Target Market(s)

people seeking counselling and psychotherapy

Font styles to use
Other font styles liked:
• Great Vibes as in our logo for some of the print. See attached file.

Requirements
Must have
• good photograph
• Two high res Pixavend photos:
• https://pixavend-files.example-cdn.net/download?id=a81kd93jf02mdl47xq
• https://pixavend-files.example-cdn.net/download?id=z57pw20ne84bvc13ty
Nice to have
• Watermark in keeping with our logo.
Should not have
• Darkness

```html
<!DOCTYPE html>
<html lang="en">
<head>
<meta charset="utf-8">
<title>Wellbrook Talking Therapies Hub – Magazine Advert</title>
<link rel="stylesheet" href="https://fonts.googleapis.com/css2?family=Great+Vibes&family=Montserrat:wght@400;500;600&display=swap">
<style>
  :root {
    --backdrop: #e9e9e9;
    --cream: #f2ecdd;
    --brown: #3e3230;
    --white: #ffffff;
    --sage: #a9bb8c;
    --olive: #7d8c2a;
    --phone-green: #86a56e;
    --ink: #2f2624;
  }
  * { margin: 0; padding: 0; box-sizing: border-box; }
  html, body { width: 1200px; height: 1200px; overflow: hidden; background: var(--backdrop); }
  .canvas { position: relative; width: 1200px; height: 1200px; }
  .advert {
    position: absolute; left: 204px; top: 40px;
    width: 792px; height: 1121px;
    background: var(--cream);
    box-shadow: 0 8px 30px rgba(0,0,0,0.12);
    overflow: hidden;
  }
  .advert-shapes { position: absolute; inset: 0; width: 100%; height: 100%; }
  .headline {
    position: absolute; left: 0; width: 100%; top: 508px;
    text-align: center;
    font-family: "Great Vibes", cursive;
    font-weight: 400; font-size: 50px; line-height: 58px;
    color: var(--ink);
  }
  .intro {
    position: absolute; left: 165px; top: 672px; width: 320px;
    font-family: "Montserrat", sans-serif;
    font-size: 16px; line-height: 23.5px; color: var(--ink);
  }
  .intro .highlight { color: var(--olive); font-weight: 600; }
  .contact {
    position: absolute; left: 64px; top: 933px;
    font-family: "Montserrat", sans-serif; color: var(--white);
  }
  .contact .hours { font-size: 14px; line-height: 17px; font-weight: 500; }
  .contact .phone { font-size: 31px; line-height: 36px; color: var(--phone-green); margin-top: 2px; letter-spacing: 0.5px; }
  .contact .address { font-size: 13px; line-height: 17px; margin-top: 10px; }
  .contact .web { font-size: 14px; font-weight: 600; margin-top: 15px; }
  .brand {
    position: absolute; left: 380px; width: 370px; top: 918px;
    text-align: center;
    font-family: "Montserrat", sans-serif; font-weight: 500;
    font-size: 21px; line-height: 28px; color: var(--brown);
  }
  .brand .brand-dot {
    display: block; width: 60px; height: 60px; margin: 0 auto 26px;
    border-radius: 50%; background: var(--sage);
  }
</style>
</head>
<body>
<div class="canvas">
  <div class="advert">
    <svg class="advert-shapes" viewBox="0 0 777 1100" preserveAspectRatio="none">
      <defs>
        <linearGradient id="sessionPhotoTone" x1="0" y1="0" x2="1" y2="1">
          <stop offset="0" stop-color="#ecebe8"/>
          <stop offset="0.35" stop-color="#d9d7d3"/>
          <stop offset="0.6" stop-color="#a9adb0"/>
          <stop offset="0.85" stop-color="#c9a893"/>
          <stop offset="1" stop-color="#8f94a0"/>
        </linearGradient>
        <linearGradient id="teamPhotoTone" x1="0" y1="0" x2="1" y2="0">
          <stop offset="0" stop-color="#e6e4e4"/>
          <stop offset="0.45" stop-color="#dcbcb4"/>
          <stop offset="0.75" stop-color="#ebe6e2"/>
          <stop offset="1" stop-color="#a9d4c6"/>
        </linearGradient>
      </defs>

      <path class="sage-band" fill="var(--sage)"
        d="M380,455 C560,445 690,380 777,260 L777,325 C700,410 560,452 380,455 Z"/>
      <path class="session-photo" role="img" aria-label="Photo of a counsellor and client seated on comfortable sofas, talking" fill="url(#sessionPhotoTone)"
        d="M0,0 L777,0 L777,260 C690,380 560,445 420,452 C280,458 140,440 0,545 Z"/>

      <path class="team-photo" role="img" aria-label="Photo of two smiling therapists in a bright consulting room" fill="url(#teamPhotoTone)"
        d="M410,836 C480,735 600,648 777,614 L777,700 C700,775 610,832 410,836 Z"/>

      <path class="lower-panel" fill="var(--white)"
        d="M410,836 C610,832 700,775 777,700 L777,1100 L320,1100 C330,1020 330,900 410,836 Z"/>

      <path class="contact-panel" fill="var(--brown)"
        d="M0,915 C100,855 250,830 410,834 C345,880 335,960 332,1010 C330,1060 322,1100 320,1100 L0,1100 Z"/>
    </svg>

    <h1 class="headline">Confidential Therapeutic Services<br>in the Heart of Old Town</h1>

    <p class="intro">We have over <span class="highlight">30 carefully selected, qualified and professional therapists</span> offering a range of services to help individuals, families and couples.</p>

    <div class="contact">
      <p class="hours">Appointments available<br>throughout the day and evening</p>
      <p class="phone">01793 620418</p>
      <p class="address">14 Linden Row, Old Town,<br>Swindon SN1 9QT</p>
      <p class="web">www.wbtth-swindon.co.uk</p>
    </div>

    <div class="brand">
      <span class="brand-dot"></span>
      Wellbrook Talking Therapies Hub
    </div>
  </div>
</div>
</body>
</html>
```